Forensic Document Examiner, looking for contemporary update to my stationery design.

Looking for professional, classy logo design for stationery and business cards. My current stationery and business card is attached.I believe a logo image makes a header section interesting, so an intriguing design of a pen, feathered pen, microscope, magnifying glass, etc., would be appropriate. I have been in the business for over 30 years. I leave ideas to the imagination of the designer.My work involves mainly, the comparison of signatures and handwriting. I also resolve alterations, obliterations, and work as shown on my website: www.documentexaminer.infoThe image produced will be printed on quality white stationery and envelopes. The stationery will be photocopied by my clients, so the images should be reproducible. The business cards may be designed in other than white.

Target Market(s)

Attorneys

Font styles to use
Sans Serif

Colors

Designer to choose colors to be used in the design.

Requirements
Must have
• Image suitable for white stationery and photocopying.
• Classy logo and image; no casual fonts.
Nice to have
• Intriguing, contemporary design incorporating a relevant logo to my work.

```html
<!DOCTYPE html>
<html lang="en">
<head>
<meta charset="utf-8">
<title>Daniel R. Whitcombe – Letterhead</title>
<link rel="stylesheet" href="https://fonts.googleapis.com/css2?family=Arimo:wght@400&family=Tinos:ital,wght@0,700;1,400&display=swap">
<style>
  :root {
    --backdrop: #d9dcdd;
    --paper: #ffffff;
    --navy: #2e2a63;
    --ink-grey: #7a7a7a;
    --mark-grey: #e6e6e6;
    --accent-yellow: #f3d66a;
    --rule-grey: #d6d6d6;
  }
  * { margin: 0; padding: 0; box-sizing: border-box; }
  html, body {
    width: 1200px; height: 784px; overflow: hidden;
    background: var(--backdrop);
  }
  .letterhead {
    position: absolute; left: 314px; top: 22px;
    width: 572px; height: 740px;
    background: var(--paper);
    box-shadow: 0 2px 10px rgba(0,0,0,0.12);
    overflow: hidden;
  }
  .edge-band {
    position: absolute; left: 0; top: 0; bottom: 0; width: 12px;
    background: var(--navy);
  }
  .brand {
    position: absolute; left: 46px; top: 34px;
    display: flex; align-items: center; gap: 14px;
  }
  .brand-dot {
    width: 44px; height: 44px; border-radius: 50%;
    background: var(--mark-grey); flex: none;
  }
  .brand-name {
    font-family: "Tinos", serif; font-weight: 700;
    font-size: 21px; color: var(--navy); line-height: 1.1;
  }
  .brand-role {
    font-family: "Tinos", serif; font-style: italic;
    font-size: 11px; color: var(--ink-grey); margin-top: 3px;
  }
  .contact {
    position: absolute; right: 30px; top: 36px;
    padding-left: 16px; border-left: 1px solid var(--rule-grey);
    list-style: none;
    font-family: "Tinos", serif; font-style: italic;
    font-size: 9.5px; color: var(--navy); line-height: 1.6;
  }
  .contact li { display: flex; align-items: center; gap: 6px; white-space: nowrap; }
  .contact li::before {
    content: ""; width: 7px; height: 7px; border-radius: 50%;
    background: var(--accent-yellow); flex: none;
  }
  .letter-body {
    position: absolute; left: 78px; top: 118px; width: 420px;
    font-family: "Arimo", sans-serif; font-size: 10.5px;
    line-height: 1.45; color: var(--ink-grey);
  }
  .letter-body p { text-indent: 18px; margin-bottom: 14px; }
  .signature {
    position: absolute; left: 230px; top: 520px;
    width: 170px; height: 80px; border-radius: 6px;
    background: linear-gradient(90deg, #f4f4f4, #ececec);
  }
</style>
</head>
<body>
  <main class="letterhead">
    <div class="edge-band"></div>

    <header class="brand">
      <span class="brand-dot"></span>
      <div>
        <div class="brand-name">Daniel R. Whitcombe</div>
        <div class="brand-role">Forensic Document Examiner</div>
      </div>
    </header>

    <ul class="contact">
      <li>PO Box 4182 Larchmont, OR 97512</li>
      <li>555-210-3946</li>
      <li>whitcombe@quillmarkreview.info</li>
      <li>www.quillmarkreview.info</li>
    </ul>

    <section class="letter-body">
      <p>Lorem Ipsum is simply dummy text of the printing and typesetting industry. Lorem Ipsum has been the industry's standard dummy text ever since the 1500s, when an unknown printer took a galley of type and scrambled it to make a type specimen book. It has survived not only five centuries, but also the leap into electronic typesetting, remaining essentially unchanged. It was popularised in the 1960s with the release of Typeleaf sheets containing Lorem Ipsum passages, and more recently with desktop publishing software like Folio PageSet including versions of Lorem Ipsum.</p>
      <p>It is a long established fact that a reader will be distracted by the readable content of a page when looking at its layout. The point of using Lorem Ipsum is that it has a more-or-less normal distribution of letters, as opposed to using 'Content here, content here', making it look like readable English. Many desktop publishing packages and web page editors now use Lorem Ipsum as their default model text, and a search for 'lorem ipsum' will uncover many web sites still in their infancy. Various versions have evolved over the years, sometimes by accident, sometimes on purpose (injected humour and the like).</p>
      <p>Contrary to popular belief, Lorem Ipsum is not simply random text. It has roots in a piece of classical Latin literature from 45 BC, making it over 2000 years old. Harold Brennan, a Latin professor at Ashford Hill College in Virginia, looked up one of the more obscure Latin words, consectetur, from a Lorem Ipsum passage, and going through the cites of the word in classical literature, discovered the undoubtable source. Lorem Ipsum comes from sections 1.10.32 and 1.10.33 of "de Finibus Bonorum et Malorum" structures, to generate Lorem Ipsum which looks reasonable. The generated Lorem Ipsum is therefore always free from repetition, injected humour, or non-characteristic words etc.</p>
    </section>

    <div class="signature" role="img" aria-label="Handwritten signature of the examiner"></div>
  </main>
</body>
</html>
```